Business Card Design for Vintage Jazz

I am a vintage jazz band leader in New York City. My groups play the music of the 1920s, 1930s and 1940s. My website is morvalquist.com for more info on what I do.

I am looking for a two sided business card design that has the look and feel of a really nice business card from the 1930s. I need to convey with the design that my work has that vintage kind of class and style, but also conveys that we are fun and entertaining.

Most importantly it should make a bold staement. If Hal Denbrook had a card, what would it have looked like? I want a card that I feel confident will make an impact and will let people know that my work is te the top that NYC has to offer in vintage jazz..

Note that I have only decided to avoid the "committed payment" option as I have not used this service before. Assuming that I get quality work I will select a design from those presented.

Target Market(s)

people who want to hire my band for events, media, and new fans of the band

Industry/Entity Type

Performing Art

Contact Information for Business Card

Definitely a matte finish, possibly a sort of old style of paper with that brown tint? definitely a thick card.

Requirements
Must have
• FRONT
• My name: Tobin Vashley
• What I do: Bandleader, Guitarist, Vocalist, Songwriter
• Contact Details: morvalquist.com tobin@morvalquist.com 646-555-0148
• BACK
• My Social Media Links:
• facebook.morvalquist.com
• twitter, instagram, linkedin: morvalquist
• I'm also including a photo image I would like to use. The photo's background is not needed, and to be honest isn't really desireable. Just looking to use the image of me.
Nice to have
• I'm attaching which could be used as is, omitted from the card, or altered maybe with text going around the outside of the circle or in some other way. It may need some clean up to the edges of the lettering as we only use it for the website thumbnail.
• If there's space I'd like to include the text "join our mailing list for a free song download: freesong.morvalquist.com" If not perhaps just "Download a Free Song at: freesong.morvalquist.com - something to this end.
Should not have
• anything cartoony. Don't think retro 90s's vision of the swing era, think actual swing era!
• anything modern. Got to look old school
• Try to avoid dark backgrounds. Since we often play in bars and clubs where it is dar, a d
• avoid script fonts.

```html
<!DOCTYPE html>
<html lang="en">
<head>
<meta charset="utf-8">
<title>Tobin Vashley – Business Card</title>
<link href="https://fonts.googleapis.com/css2?family=Josefin+Sans:wght@400;600;700&family=Libre+Baskerville:wght@400;700&display=swap" rel="stylesheet">
<style>
  :root {
    --paper: #f4ecda;
    --paper-deep: #e9dcc0;
    --ink: #1e1a15;
    --ink-soft: #4a4036;
    --rule: #2a241d;
    --backdrop: #e6e2dc;
    --photo-light: #d8ccb6;
    --photo-dark: #3b332a;
  }
  * { margin: 0; padding: 0; box-sizing: border-box; }
  html, body {
    width: 1200px; height: 900px; overflow: hidden;
    background: var(--backdrop);
  }
  .stage { position: relative; width: 1200px; height: 900px; }

  .card {
    position: absolute;
    background: var(--paper);
    overflow: hidden;
    box-shadow: 0 6px 18px rgba(0,0,0,0.16);
    color: var(--ink);
  }
  .card::after {
    content: ""; position: absolute; inset: 10px;
    border: 1px solid var(--rule);
    outline: 1px solid var(--rule); outline-offset: -5px;
    pointer-events: none;
  }
  .card-front { left: 78px; top: 35px; width: 588px; height: 363px; }
  .card-back  { left: 388px; top: 506px; width: 567px; height: 350px; }

  .band {
    position: absolute; left: 0; right: 0; bottom: 0;
    background: var(--paper-deep);
    border-top: 3px double var(--rule);
  }
  .card-front .band { top: 155px; }
  .card-back .band  { top: 190px; }

  .portrait {
    position: absolute; left: 300px; top: 0; width: 288px; height: 363px;
    background: linear-gradient(160deg, var(--photo-light) 0%, #9b8c76 50%, var(--photo-dark) 100%);
  }

  .identity { position: absolute; left: 31px; top: 170px; width: 262px; }
  .identity-name {
    font-family: "Josefin Sans", "Century Gothic", sans-serif;
    font-size: 25px; font-weight: 700; letter-spacing: 1.5px; line-height: 1.2;
  }
  .contact-list {
    list-style: none; margin-top: 12px;
    font-family: "Libre Baskerville", Georgia, serif;
    font-size: 13px; line-height: 21px; color: var(--ink-soft);
  }
  .contact-label { font-weight: 700; color: var(--ink); }
  .roles {
    margin-top: 12px;
    font-family: "Josefin Sans", "Century Gothic", sans-serif;
    font-size: 15px; font-weight: 700; line-height: 22px; letter-spacing: 0.6px;
    text-transform: uppercase;
  }

  .brand {
    position: absolute; left: 46px; top: 72px;
    display: flex; align-items: center; gap: 14px;
    font-family: "Josefin Sans", "Century Gothic", sans-serif;
    font-size: 28px; font-weight: 700; letter-spacing: 1px; color: var(--ink);
  }
  .brand-mark {
    width: 36px; height: 36px; border-radius: 50%;
    border: 2px solid var(--ink);
  }

  .social-list {
    position: absolute; left: 29px; top: 212px;
    list-style: none;
    font-family: "Libre Baskerville", Georgia, serif;
    font-size: 14px; line-height: 26px; color: var(--ink);
  }
  .social-item { display: flex; align-items: center; gap: 8px; }
  .social-marker { width: 11px; height: 11px; background: var(--ink); }
</style>
</head>
<body>
<main class="stage">

  <section class="card card-front" aria-label="Card front">
    <div class="band"></div>
    <div class="portrait" role="img" aria-label="Black and white photo of the bandleader tipping a straw boater hat, wearing a dark piped blazer"></div>
    <div class="identity">
      <h1 class="identity-name">TOBIN VASHLEY</h1>
      <ul class="contact-list">
        <li><span class="contact-label">Phone:</span> 646-555-0148</li>
        <li><span class="contact-label">Email:</span> tobin@morvalquist.com</li>
        <li><span class="contact-label">Website:</span> morvalquist.com</li>
      </ul>
      <p class="roles">Bandleader, Guitarist,<br>Vocalist, Songwriter</p>
    </div>
  </section>

  <section class="card card-back" aria-label="Card back">
    <div class="brand">
      <span class="brand-mark"></span>
      <span class="brand-name">Tobin Vashley</span>
    </div>
    <div class="band"></div>
    <ul class="social-list">
      <li class="social-item"><span class="social-marker"></span>morvalquist.com</li>
      <li class="social-item"><span class="social-marker"></span>morvalquist</li>
      <li class="social-item"><span class="social-marker"></span>morvalquist</li>
      <li class="social-item"><span class="social-marker"></span>morvalquist</li>
    </ul>
  </section>

</main>
</body>
</html>
```